Product packaging design for lentils

Looking to create a design for lentils in 4lb format. We are looking to create a base design for the bags, and then from there will have additional designs for the different products with different product name, barcodes and nutritional information.

Industry/Entity Type

Food

```html
<!DOCTYPE html>
<html lang="en">
<head>
<meta charset="utf-8">
<title>Greenmeal Lentils Pouch</title>
<link rel="stylesheet" href="https://fonts.googleapis.com/css2?family=Mulish:wght@400;700;800&family=Nunito:wght@800&display=swap">
<style>
  :root {
    --bg: #cfcfcf;
    --pouch-white: #f4f4f4;
    --brand-green: #6aab34;
    --dot-green: #9fcb6b;
    --ink: #3a3a3a;
    --lentil-dark: #a55a32;
    --lentil-mid: #c07a52;
    --lentil-light: #d9a689;
    --band-light: #e2a57a;
    --band-mid: #c9793f;
    --band-dark: #b4622c;
    --band-text: #fbe9dc;
  }
  * { margin: 0; padding: 0; box-sizing: border-box; }
  html, body { width: 1200px; height: 800px; overflow: hidden; }
  body {
    background: var(--bg);
    font-family: "Mulish", sans-serif;
    position: relative;
  }
  .pouch {
    position: absolute;
    left: 410px; top: 120px;
    width: 380px; height: 560px;
    background: var(--pouch-white);
    overflow: hidden;
  }
  .dot-pattern {
    position: absolute;
    left: 52px; top: 0;
    width: 103px; height: 312px;
    background: linear-gradient(180deg, rgba(159,203,107,0.55), rgba(159,203,107,0.25));
  }
  .brand {
    position: absolute;
    left: 200px; top: 193px;
    width: 150px;
    display: flex; align-items: center; justify-content: center; gap: 6px;
  }
  .brand-dot {
    width: 12px; height: 12px; border-radius: 50%;
    background: var(--brand-green);
  }
  .brand-name {
    font-family: "Mulish", sans-serif;
    font-weight: 800;
    font-size: 20px;
    color: var(--brand-green);
  }
  .product-name {
    position: absolute;
    left: 219px; top: 246px;
    font-family: "Mulish", sans-serif;
    font-weight: 700;
    font-size: 40px;
    letter-spacing: -1px;
    line-height: 1;
    color: var(--ink);
  }
  .product-underline {
    position: absolute;
    left: 221px; top: 291px;
    width: 96px; height: 2px;
    background: var(--brand-green);
  }
  .lentil-window {
    position: absolute;
    left: 0; top: 312px;
    width: 380px; height: 120px;
    background: linear-gradient(110deg, var(--lentil-light) 0%, var(--lentil-mid) 45%, var(--lentil-dark) 100%);
  }
  .info-band {
    position: absolute;
    left: 0; top: 432px;
    width: 380px; height: 128px;
    background: linear-gradient(100deg, var(--band-light) 0%, var(--band-mid) 50%, var(--band-dark) 100%);
    color: var(--band-text);
  }
  .description {
    position: absolute;
    left: 70px; top: 20px;
    width: 242px;
    font-size: 5px;
    line-height: 1.3;
  }
  .benefits {
    position: absolute;
    left: 70px; top: 56px;
    width: 242px;
    display: flex; align-items: center; justify-content: space-between;
    font-size: 7px;
  }
  .benefit { display: flex; align-items: center; gap: 2px; }
  .benefit svg { width: 14px; height: 14px; }
  .sep { width: 1px; height: 3px; background: var(--band-text); }
  .net-weight {
    position: absolute;
    right: 70px; top: 92px;
    font-weight: 700;
    font-size: 10px;
  }
</style>
</head>
<body>
  <div class="pouch">
    <div class="dot-pattern" role="img" aria-label="Green dot pattern column"></div>

    <div class="brand">
      <span class="brand-dot"></span>
      <span class="brand-name">Greenmeal</span>
    </div>

    <div class="product-name">lentils</div>
    <div class="product-underline"></div>

    <div class="lentil-window" role="img" aria-label="Window showing red lentils inside the bag"></div>

    <div class="info-band">
      <p class="description">Our red lentils are carefully sorted and cleaned for a soft bite and quick cooking. Rinse well, simmer in salted water for about fifteen minutes and enjoy in soups, curries and salads. Store sealed in a cool, dry place away from light after opening.</p>

      <div class="benefits">
        <span class="benefit">
          <svg viewBox="0 0 14 14" fill="none" stroke="currentColor" stroke-width="0.8"><circle cx="7" cy="7" r="5.5"/><path d="M4 9c1-4 4-5 6-5-0 3-2 6-6 5z"/></svg>
          Fresh
        </span>
        <span class="sep"></span>
        <span class="benefit">
          <svg viewBox="0 0 14 14" fill="none" stroke="currentColor" stroke-width="0.8"><path d="M7 2v10M7 5l-2-2M7 5l2-2M7 8l-2-2M7 8l2-2"/></svg>
          High Fiber
        </span>
        <span class="sep"></span>
        <span class="benefit">
          <svg viewBox="0 0 14 14" fill="none" stroke="currentColor" stroke-width="0.8"><path d="M7 1.5C5 5 3.5 7 3.5 9a3.5 3.5 0 0 0 7 0C10.5 7 9 5 7 1.5z"/></svg>
          Low Fat
        </span>
        <span class="sep"></span>
        <span class="benefit">
          <svg viewBox="0 0 14 14" fill="none" stroke="currentColor" stroke-width="0.8"><path d="M7 12S1.5 8.5 1.5 5A2.8 2.8 0 0 1 7 4a2.8 2.8 0 0 1 5.5 1C12.5 8.5 7 12 7 12z"/><path d="M4.8 6.6l1.6 1.6 3-3"/></svg>
          Heart Health
        </span>
      </div>

      <div class="net-weight">15g</div>
    </div>
  </div>
</body>
</html>
```